Design a WordPress layout for a home loans company

The home loans company in question is going through a rebrand and needs a new website layout.
Sites they like: http://www.brightkeylending.com.au/
Current logo: Attached.
Colours to be used: As per those used in logo.
Primary: #71aa3d
Secondary: #130e10
Pages to be designed:
- Homepage
- Internal services page
Menu items for display purposes:
- Home
- About Us
- Speak to a Broker
- Articles
- Contact Us
A modern design with simplicity is key.
For copy, dummy text such as Lorem ipsum will be fine.
If you would like anything elso, please ask.
Target Market(s)
25-40 year old
Mostly female
Buying their first home in most cases
Industry/Entity Type
Mortgage Brokerage
Number of Pages Required
2 page

```html
<!DOCTYPE html>
<html lang="en">
<head>
<meta charset="utf-8">
<title>Harbourline Home Loans</title>
<link href="https://fonts.googleapis.com/css2?family=Montserrat:wght@300;400;500;600;700&display=swap" rel="stylesheet">
<style>
:root{
  --green:#71aa3d;
  --green-dark:#4f7a2b;
  --ink:#130e10;
  --nav-active:#2a2527;
  --grey-bg:#f1f1f1;
  --text:#555;
  --muted:#888;
  --line:#cfcfcf;
  --white:#fff;
}
*{margin:0;padding:0;box-sizing:border-box}
html,body{width:1200px;height:3516px;overflow:hidden}
body{font-family:'Montserrat',sans-serif;color:var(--ink);background:var(--white);position:relative}
.abs{position:absolute}
/* header */
.site-header{position:absolute;left:0;top:0;width:1200px;height:94px;background:var(--white)}
.brand{left:77px;top:26px;display:flex;align-items:center;gap:10px;font-weight:700;font-size:30px;color:var(--green)}
.brand-square{width:22px;height:22px;background:var(--green)}
.tollfree{left:684px;top:20px;display:flex;align-items:center;gap:12px}
.tollfree .ring{width:46px;height:46px;border:2px solid var(--green);border-radius:50%;display:flex;align-items:center;justify-content:center}
.tollfree small{display:block;font-size:15px;font-weight:500}
.tollfree strong{display:block;font-size:22px;font-weight:600;color:var(--green)}
.search{left:907px;top:20px;width:214px;height:48px;border:1px solid #e3e3e3;border-radius:24px;display:flex;align-items:center;justify-content:space-between;padding:0 20px;font-size:12px;color:#aaa;box-shadow:0 2px 6px rgba(0,0,0,.08)}
/* nav */
.main-nav{position:absolute;left:0;top:94px;width:1200px;height:51px;background:var(--green)}
.main-nav a{position:absolute;top:0;height:51px;line-height:51px;color:var(--white);font-size:15px;text-decoration:none;text-transform:uppercase}
.main-nav .active{background:var(--nav-active);left:77px;width:129px;text-align:center}
.main-nav .apply{background:var(--green-dark);left:940px;width:183px;text-align:center;font-size:17px}
/* hero */
.hero{position:absolute;left:0;top:145px;width:1200px;height:575px;background:linear-gradient(90deg,#f4efe6 0%,#e8d7b7 35%,#c9a874 60%,#8e8a55 100%)}
.hero-copy{left:79px;top:322px}
.hero-copy p{font-size:18px;font-weight:500}
.hero-copy h1{margin-top:14px;font-size:40px;line-height:1.12;font-weight:700;text-transform:uppercase;letter-spacing:.5px}
.hero-copy h1 span{font-size:54px}
.btn{display:inline-block;height:60px;line-height:60px;text-align:center;color:var(--white);font-size:18px;text-transform:uppercase;text-decoration:none}
.btn-green{background:var(--green)}
.btn-dark{background:var(--ink)}
/* section heads */
.section-title{position:absolute;left:0;width:1200px;text-align:center;font-weight:600;font-size:40px;white-space:nowrap}
.section-title em{font-style:normal;color:var(--green);font-size:60px;font-weight:700;text-transform:uppercase;letter-spacing:1px}
.section-sub{position:absolute;left:0;width:1200px;text-align:center;font-size:17px;color:var(--text)}
/* welcome */
.welcome-art{left:290px;top:760px;width:620px;height:330px;background:linear-gradient(180deg,#fafafa,#f4f4f4)}
.welcome-text{left:183px;top:900px;width:834px;text-align:center;font-size:15px;line-height:20px;color:var(--text)}
/* choose */
.choose{position:absolute;left:0;top:1177px;width:1200px;height:701px;background:var(--grey-bg)}
.choose-photo{left:77px;top:1388px;width:333px;height:424px;background:linear-gradient(135deg,#dfe6ea,#b7c3c9 50%,#6f5a48)}
.choose-lead{left:449px;top:1398px;width:290px;text-align:center;font-size:14.5px;line-height:25px;color:var(--text)}
.feature{position:absolute;width:291px;text-align:center}
.feature .icon{width:73px;height:70px;margin:0 auto;background:var(--green);display:flex;align-items:center;justify-content:center}
.feature h3{margin-top:22px;font-size:22px;font-weight:600}
.feature p{margin-top:14px;font-size:12.5px;line-height:19px;color:var(--text)}
/* brokers */
.brokers{position:absolute;left:0;top:1878px;width:1200px;height:508px;background:var(--green)}
.broker-card{position:absolute;top:2166px;width:254px;height:143px;background:var(--white);border:4px solid #333;text-align:center;padding-top:30px}
.broker-card h4{color:var(--green);font-size:20px;font-weight:700}
.broker-card small{display:block;margin-top:8px;font-size:13px;color:var(--muted)}
.broker-card a{display:inline-block;margin-top:8px;font-size:17px;color:var(--green);text-decoration:underline}
.broker-photo{position:absolute;top:2081px;width:110px;height:115px;background:var(--white);padding:6px;box-shadow:0 2px 6px rgba(0,0,0,.25)}
.broker-photo div{width:100%;height:100%;background:linear-gradient(180deg,#c9c9c9,#6b6b6b)}
.arrow{position:absolute;top:2168px;width:40px;height:42px;border:2px solid var(--white);display:flex;align-items:center;justify-content:center}
/* contact */
.contact-bg{position:absolute;left:0;top:2386px;width:1200px;height:492px;background:var(--grey-bg)}
.field{position:absolute;border:1px solid var(--line);background:var(--grey-bg);font-size:13px;color:#aaa;padding:12px 14px}
/* articles */
.article-img{position:absolute;top:3031px;width:235px;height:211px}
.article-body{position:absolute;top:3028px;width:262px}
.article-body h5{font-size:16px;font-weight:700;line-height:23px}
.article-body .date{margin-top:16px;padding:12px 0;border-top:1px solid #e5e5e5;border-bottom:1px solid #e5e5e5;font-size:15px;color:var(--muted);display:flex;align-items:center;gap:12px}
.article-body p{margin-top:14px;font-size:13px;line-height:19px;color:var(--muted)}
.article-body a{display:inline-block;margin-top:14px;font-size:14px;color:var(--green);text-decoration:underline;text-transform:uppercase}
/* footer */
.site-footer{position:absolute;left:0;top:3310px;width:1200px;height:206px;background:var(--green);color:var(--white)}
.foot-item{position:absolute;top:48px;display:flex;align-items:center;gap:18px;font-size:15px;line-height:20px}
.foot-item .ring{width:48px;height:48px;border:2px solid rgba(255,255,255,.8);border-radius:50%;display:flex;align-items:center;justify-content:center}
.foot-rule{position:absolute;left:77px;top:136px;width:1046px;height:1px;background:rgba(255,255,255,.35)}
.copyright{position:absolute;left:0;top:164px;width:1200px;text-align:center;font-size:13px;color:var(--ink)}
.copyright b{font-size:17px}
</style>
</head>
<body>

<header class="site-header">
  <div class="abs brand"><span class="brand-square"></span>Harbourline</div>
  <div class="abs tollfree">
    <div class="ring"><svg width="22" height="22" viewBox="0 0 24 24"><path d="M6.6 10.8a15 15 0 0 0 6.6 6.6l2.2-2.2c.3-.3.7-.4 1-.2 1.1.4 2.3.6 3.6.6.6 0 1 .4 1 1V20c0 .6-.4 1-1 1A17 17 0 0 1 3 4c0-.6.4-1 1-1h3.5c.6 0 1 .4 1 1 0 1.3.2 2.5.6 3.6.1.3 0 .7-.2 1z" fill="#333"/></svg></div>
    <div><small>Call Toll free No.</small><strong>555 014 2290</strong></div>
  </div>
  <div class="abs search">Search here...<svg width="26" height="26" viewBox="0 0 24 24"><circle cx="10" cy="10" r="7" fill="none" stroke="#1c2a4a" stroke-width="2.6"/><path d="M15 15l6 6" stroke="#1c2a4a" stroke-width="3"/></svg></div>
</header>

<nav class="main-nav">
  <a class="active">Home</a>
  <a style="left:243px">About</a>
  <a style="left:380px">Speak to a Broker</a>
  <a style="left:627px">Articles</a>
  <a style="left:783px">Contact</a>
  <a class="apply">Apply Now</a>
</nav>

<section class="hero" role="img" aria-label="Photo of a young couple standing in front of a new house at sunset"></section>
<div class="abs hero-copy">
  <p>98 % Customer Satisfied with us.</p>
  <h1>Are you looking<br>for <span>Home loan?</span></h1>
  <div style="margin-top:22px;display:flex;gap:9px">
    <a class="btn btn-green" style="width:228px">Find out more</a>
    <a class="btn btn-dark" style="width:192px">Apply now</a>
  </div>
</div>

<div class="abs welcome-art" role="img" aria-label="Faint illustration of a house"></div>
<h2 class="section-title" style="top:805px">Welcome To <em>Harbourline Loans</em></h2>
<p class="abs welcome-text">Lorem Ipsum is simply dummy text of the printing and typesetting industry. Lorem Ipsum has been the industry's standard dummy text ever since the 1500s, when an unknown printer took a galley of type and scrambled it to make a type specimen book. It has survived not only five centuries, but also the leap into electronic typesetting, remaining essentially unchanged. It was popularised in the 1960s.</p>
<a class="abs btn btn-dark" style="left:504px;top:1008px;width:192px;height:59px;line-height:59px">Learn more</a>

<section class="choose"></section>
<h2 class="section-title" style="top:1232px">Reason To <em>Choose us</em></h2>
<p class="section-sub" style="top:1325px">With a Harbourline Home Loans broker, you'll have:</p>
<div class="abs choose-photo" role="img" aria-label="Photo of a smiling couple receiving house keys"></div>
<p class="abs choose-lead">Your Harbourline Home Loans broker comes to you, free of charge, and works with you through all aspects of your home loan application, right through to being handed the keys.</p>

<div class="feature" style="left:811px;top:1388px">
  <div class="icon"><svg width="32" height="32" viewBox="0 0 24 24"><rect x="5" y="3" width="14" height="18" rx="1" fill="none" stroke="#fff" stroke-width="1.6"/><path d="M12 7a3 3 0 0 0-3 3c0 2 3 5 3 5s3-3 3-5a3 3 0 0 0-3-3z" fill="#fff"/></svg></div>
  <h3>Local experts</h3>
  <p>With brokers all across Australia, you can be confident there is a professional near you with in-depth knowledge of your local area.</p>
</div>
<div class="feature" style="left:453px;top:1622px">
  <div class="icon"><svg width="34" height="32" viewBox="0 0 26 24"><path d="M3 4h14v9H8l-4 3v-3H3z M9 15v2h9l4 3v-3h1V8h-4" fill="none" stroke="#fff" stroke-width="1.5" stroke-linejoin="round"/></svg></div>
  <h3>Ongoing trusted advice</h3>
  <p>With brokers all across Australia, you can be confident there is a professional near you with in-depth knowledge of your local area.</p>
</div>
<div class="feature" style="left:811px;top:1622px">
  <div class="icon"><svg width="32" height="32" viewBox="0 0 24 24"><path d="M3 10h4v11H3z M9 20V10l4-7c1.5 0 2 1 2 2l-1 4h6c1 0 2 1 1.7 2.2l-1.8 7C19.6 19.4 19 20 18 20z" fill="none" stroke="#fff" stroke-width="1.6" stroke-linejoin="round"/></svg></div>
  <h3>Greater choice</h3>
  <p>With brokers all across Australia, you can be confident there is a professional near you with in-depth knowledge of your local area.</p>
</div>

<section class="brokers"></section>
<h2 class="section-title" style="top:1931px">Meet <em style="color:#fff">Our broker</em></h2>
<p class="section-sub" style="top:2022px;font-size:14px;color:var(--ink)">Meet our best broker,our team of agents are ready to help you.</p>
<div class="arrow" style="left:14px"><svg width="14" height="14" viewBox="0 0 14 14"><path d="M9 2L4 7l5 5" fill="none" stroke="#fff" stroke-width="2"/></svg></div>
<div class="arrow" style="left:1139px"><svg width="14" height="14" viewBox="0 0 14 14"><path d="M5 2l5 5-5 5" fill="none" stroke="#fff" stroke-width="2"/></svg></div>

<div class="broker-card" style="left:98px"><h4>BROKER NAME</h4><small>Designation</small><a>LEARN MORE</a></div>
<div class="broker-photo" style="left:300px"><div role="img" aria-label="Broker portrait photo"></div></div>
<div class="broker-card" style="left:445px"><h4>BROKER NAME</h4><small>Designation</small><a>LEARN MORE</a></div>
<div class="broker-photo" style="left:645px"><div role="img" aria-label="Broker portrait photo"></div></div>
<div class="broker-card" style="left:790px"><h4>BROKER NAME</h4><small>Designation</small><a>LEARN MORE</a></div>
<div class="broker-photo" style="left:989px"><div role="img" aria-label="Broker portrait photo"></div></div>

<section class="contact-bg"></section>
<h2 class="section-title" style="top:2442px">Contact <em>An expert</em></h2>
<p class="section-sub" style="top:2530px">With a Harbourline Home Loans broker, you'll have:</p>
<div class="field" style="left:183px;top:2578px;width:272px;height:50px">Name</div>
<div class="field" style="left:464px;top:2578px;width:272px;height:50px">E-mail</div>
<div class="field" style="left:745px;top:2578px;width:272px;height:50px">Phone</div>
<div class="field" style="left:183px;top:2639px;width:834px;height:103px">Message</div>
<a class="abs btn btn-dark" style="left:504px;top:2754px;width:192px;height:63px;line-height:63px;font-size:20px">Submit</a>

<h2 class="section-title" style="top:2934px">Latest <em>Articles</em></h2>
<div class="article-img" style="left:77px;background:linear-gradient(180deg,#9fc6e6,#e8e2d8 55%,#c98d7d)" role="img" aria-label="Photo of hands holding a small model house"></div>
<div class="article-body" style="left:323px">
  <h5>Lorem Ipsum is simply dummy text of the printing.</h5>
  <div class="date"><svg width="16" height="16" viewBox="0 0 16 16"><rect x="1" y="3" width="14" height="12" fill="none" stroke="#aaa" stroke-width="1.4"/><path d="M1 7h14M5 1v4M11 1v4" stroke="#aaa" stroke-width="1.4"/></svg>20 Jul,2018</div>
  <p>Lorem Ipsum is simply dummy text of the printing and typesetting.</p>
  <a>Read more</a>
</div>
<div class="article-img" style="left:607px;background:linear-gradient(135deg,#d9a7ae,#c47d56 50%,#e6c7c8)" role="img" aria-label="Photo of a toy house on a financial document"></div>
<div class="article-body" style="left:853px">
  <h5>Lorem Ipsum is simply dummy text of the printing.</h5>
  <div class="date"><svg width="16" height="16" viewBox="0 0 16 16"><rect x="1" y="3" width="14" height="12" fill="none" stroke="#aaa" stroke-width="1.4"/><path d="M1 7h14M5 1v4M11 1v4" stroke="#aaa" stroke-width="1.4"/></svg>10 May,2018</div>
  <p>Lorem Ipsum is simply dummy text of the printing and typesetting.</p>
  <a>Read more</a>
</div>

<footer class="site-footer">
  <div class="foot-item" style="left:190px">
    <span class="ring"><svg width="20" height="22" viewBox="0 0 20 22"><path d="M10 1a7 7 0 0 0-7 7c0 5 7 13 7 13s7-8 7-13a7 7 0 0 0-7-7z" fill="#fff"/><circle cx="10" cy="8" r="2.6" fill="#71aa3d"/></svg></span>
    <span>Lorem ipsum dolor sit amet,<br>consectetur adipiscing elit.</span>
  </div>
  <div class="foot-item" style="left:530px">
    <span class="ring"><svg width="16" height="22" viewBox="0 0 16 22"><rect x="2" y="1" width="12" height="20" rx="2" fill="none" stroke="#fff" stroke-width="1.8"/><circle cx="8" cy="17" r="1.2" fill="#fff"/></svg></span>
    <span>555 014 2290</span>
  </div>
  <div class="foot-item" style="left:725px">
    <span class="ring"><svg width="22" height="16" viewBox="0 0 22 16"><rect x="1" y="1" width="20" height="14" fill="#fff"/><path d="M1 1l10 8 10-8" fill="none" stroke="#71aa3d" stroke-width="1.6"/></svg></span>
    <span>sales@harbourlineloans.com</span>
  </div>
  <div class="foot-rule"></div>
  <p class="copyright"><b>Harbourline Home Loans</b> - 2018 All Right Reserved</p>
</footer>

</body>
</html>
```